Professional BIO Template with photo and logo

Hello,
I need a professional Bio template developed via Microsoft WORD ASAP!!!!! I would like to just be able to add the text I need to add. So resize-able text boxes. Potentially able to adjust the font. These are the things I need added it to include.
Head shot (attached)
Text Box for Name
Text Box for phone number
Text box for email
KVT Logo (attached)
Maybe a blue banner at the top or some background boxes that are blue or grey. Here are the pantone colors that our company uses.

CORE COLOR
100c 91m 17y 6k 38r 58g 128b Hex #263A80 Pantone 7687 C

CORE CONTRAST COLOR
36c 29m 28y 0k 168r 168g 170b Hex #669999 Pantone Cool Gray 6C

I also attached some examples of what we have been looking at. Instead of green add the blue...instead of black maybe just be white.

Thank you

```html
<!DOCTYPE html>
<html lang="en">
<head>
<meta charset="utf-8">
<title>Ellis Marlowe – Bio</title>
<link rel="stylesheet" href="https://fonts.googleapis.com/css2?family=Montserrat:wght@400;500;700&family=Open+Sans:wght@700&family=Lato:wght@400&display=swap">
<style>
  :root {
    --core-blue: #263a80;
    --contrast-gray: #a8a8aa;
    --rule-gray: #c8c8c8;
    --body-text: #555a60;
    --paper: #ffffff;
    --photo-light: #6a6d72;
    --photo-dark: #2a2c30;
  }
  * { margin: 0; padding: 0; box-sizing: border-box; }
  html, body { width: 940px; height: 1200px; overflow: hidden; background: var(--paper); }
  .bio-sheet { position: relative; width: 940px; height: 1200px; background: var(--paper); }

  .brand-mark {
    position: absolute; left: 79px; top: 70px; width: 248px; height: 176px;
    display: flex; align-items: center; justify-content: center; gap: 14px;
  }
  .brand-mark__square { width: 22px; height: 22px; background: var(--contrast-gray); }
  .brand-mark__name {
    font-family: "Open Sans", sans-serif; font-weight: 700; font-size: 64px;
    color: var(--core-blue); letter-spacing: 4px; line-height: 1;
  }

  .name-banner {
    position: absolute; left: 417px; top: 53px; width: 523px; height: 204px;
    background: var(--core-blue); color: var(--paper);
    font-family: "Montserrat", sans-serif;
  }
  .name-banner__first {
    position: absolute; left: 49px; top: 22px;
    font-size: 50px; font-weight: 700; line-height: 1; letter-spacing: 1px;
  }
  .name-banner__last {
    position: absolute; left: 42px; top: 82px;
    font-size: 54px; font-weight: 500; line-height: 1; letter-spacing: 1px;
  }
  .name-banner__rule {
    position: absolute; left: 42px; top: 140px; width: 363px; height: 1.5px; background: var(--paper);
  }
  .name-banner__role {
    position: absolute; left: 42px; top: 149px;
    font-size: 17px; font-weight: 500; letter-spacing: 4.6px;
  }

  .portrait {
    position: absolute; left: 0; top: 276px; width: 416px; height: 602px;
    background: radial-gradient(ellipse at 50% 35%, var(--photo-light) 0%, #4a4c51 45%, var(--photo-dark) 100%);
  }

  .contact-panel {
    position: absolute; left: 0; top: 896px; width: 413px; height: 248px;
    background: var(--core-blue); color: var(--paper);
  }
  .contact-panel__title {
    position: absolute; left: 53px; top: 6px;
    font-family: "Open Sans", sans-serif; font-weight: 700; font-size: 52px; line-height: 1.2;
  }
  .contact-panel__rule {
    position: absolute; left: 53px; top: 81px; width: 301px; height: 2px; background: var(--paper);
  }
  .contact-panel__list {
    position: absolute; left: 53px; top: 99px; list-style: none;
    font-family: "Lato", sans-serif; font-size: 21px; line-height: 37px;
  }

  .about {
    position: absolute; left: 451px; top: 278px; width: 489px;
  }
  .about__title {
    font-family: "Open Sans", sans-serif; font-weight: 700; font-size: 34px;
    color: var(--core-blue); line-height: 1.2; padding-bottom: 2px;
    border-bottom: 2px solid var(--rule-gray);
  }
  .about__body {
    width: 459px; margin-top: 10px; height: 800px; overflow: hidden;
    font-family: "Montserrat", sans-serif; font-size: 11.2px; line-height: 18.1px;
    color: var(--body-text); text-align: justify;
  }
  .about__body p + p { margin-top: 18.1px; }
</style>
</head>
<body>
<main class="bio-sheet">
  <div class="brand-mark">
    <span class="brand-mark__square"></span>
    <span class="brand-mark__name">KVT</span>
  </div>

  <header class="name-banner">
    <h1>
      <span class="name-banner__first">ELLIS</span>
      <span class="name-banner__last">MARLOWE</span>
    </h1>
    <div class="name-banner__rule"></div>
    <p class="name-banner__role">MARKETING MANAGER</p>
  </header>

  <div class="portrait" role="img" aria-label="Head shot portrait of the team member in a dark suit against a grey studio backdrop"></div>

  <section class="contact-panel">
    <h2 class="contact-panel__title">Contact</h2>
    <div class="contact-panel__rule"></div>
    <ul class="contact-panel__list">
      <li>123 - 456 -78</li>
      <li>youremail@domain.com</li>
      <li>Year, Month/Date</li>
      <li>Your City, Country</li>
    </ul>
  </section>

  <section class="about">
    <h2 class="about__title">About me</h2>
    <div class="about__body">
      <p>Lorem ipsum dolor sit amet, consectetuer adipiscing elit, sed diam nonummy nibh euismod tincidunt ut laoreet dolore magna aliquam erat volutpat. Ut wisi enim ad minim veniam, quis nostrud exerci tation ullamcorper suscipit lobortis nisl ut aliquip ex ea commodo consequat. Duis autem vel eum iriure dolor in hendrerit in vulputate velit esse molestie consequat, vel illum dolore eu feugiat nulla facilisis at vero eros et accumsan et iusto odio dignissim qui blandit praesent luptatum zzril delenit augue duis dolore te feugait nulla facilisi.</p>
      <p>Lorem ipsum dolor sit amet, cons ectetuer adipiscing elit, sed diam nonummy nibh euismod tincidunt ut laoreet dolore magna aliquam erat volutpat. Ut wisi enim ad minim veniam, quis nostrud exerci tation ullamcorper suscipit lobortis nisl ut aliquip ex ea commodo consequat. Lorem ipsum dolor sit amet, consectetuer adipiscing elit, sed diam nonummy nibh euismod tincidunt ut laoreet dolore magna aliquam erat volutpat. Ut wisi enim ad minim veniam, quis nostrud exerci tation ullamcorper suscipit lobortis nisl ut aliquip ex ea commodo consequat. Duis autem vel eum iriure dolor in hendrerit in vulputate velit esse molestie consequat, vel illum dolore eu feugiat nulla facilisis at vero eros et accumsan et iusto odio dignissim qui blandit praesent luptatum zzril delenit augue duis dolore te feugait nulla facilisi.</p>
      <p>Lorem ipsum dolor sit amet, cons ectetuer adipiscing elit, sed diam nonummy nibh euismod tincidunt ut laoreet dolore magna aliquam erat volutpat. Ut wisi enim ad minim veniam, quis nostrud exerci tation ullamcorper suscipit lobortis nisl ut aliquip ex ea commodo consequat.</p>
      <p>Lorem ipsum dolor sit amet, consectetuer adipiscing elit, sed diam nonummy nibh euismod tincidunt ut laoreet dolore magna aliquam erat volutpat. Ut wisi enim ad minim veniam, quis nostrud exerci tation ullamcorper suscipit lobortis nisl ut aliquip ex ea commodo consequat. Duis autem vel eum iriure dolor in hendrerit in vulputate velit esse molestie consequat, vel illum dolore eu feugiat nulla facilisis at vero eros et accumsan et iusto odio dignissim qui blandit praesent luptatum zzril delenit augue duis dolore te feugait nulla facilisi.</p>
      <p>Lorem ipsum dolor sit amet, cons ectetuer adipiscing elit, sed diam nonummy nibh euismod tincidunt ut laoreet dolore magna aliquam erat volutpat. Ut wisi enim ad minim veniam, quis nostrud exerci tation ullamcorper suscipit lobortis nisl ut aliquip ex ea commodo consequat. Lorem ipsum dolor sit amet, consectetuer adipiscing elit, sed diam nonummy nibh euismod tincidunt ut laoreet dolore magna aliquam erat volutpat. Ut wisi enim ad minim veniam, quis nostrud exerci tation ullamcorper suscipit lobortis nisl ut aliquip ex ea commodo consequat.</p>
    </div>
  </section>
</main>
</body>
</html>
```